Ram and co fleecing works pty ltd

We are sheep shearing contractors,we are looking for a simple design business card, with a drawing like picture of a Australian sheep on it, then just standard details, name, phone, email, po box.
We would like double sided, with 2 lines of wiriting on the back, no bright colours please.
We like black and white, doesn't have to be too serious, however nothing to far left of cwntre.
On the back of the card we would like professional shearing contract offering full contract team.
Can use use the symbol & in the name instead of and.

Target Market(s)

Sheep farmers, target males from age 20 and up

Contact Information for Business Card

Company name ram and co fleecing works pty ltd
Marcus haldenby 0471305846, po box 4072 sale vic 3853,
Email ramandcofleecing@mailbarn.example, gippsland shearing contractor

Font styles to use
Serif

Colors

Designer to choose only greyscale colors for use in the design.

Requirements
Nice to have
• Simple design

```html
<!DOCTYPE html>
<html lang="en">
<head>
<meta charset="utf-8">
<title>Ram and Co Fleecing Works – Business Card</title>
<link rel="stylesheet" href="https://fonts.googleapis.com/css2?family=Archivo:wght@400;800&display=swap">
<style>
  :root {
    --page: #e6e6e4;
    --card: #ffffff;
    --ink: #1e1e1e;
    --ink-soft: #3a3a3a;
    --rule: #b5b5b5;
    --shade: rgba(0,0,0,0.18);
    --art-light: #f4f4f4;
    --art-dark: #d2d2d2;
  }
  * { box-sizing: border-box; margin: 0; padding: 0; }
  html, body { width: 1200px; height: 900px; overflow: hidden; }
  body {
    background: var(--page);
    font-family: "Archivo", Arial, sans-serif;
    color: var(--ink);
    position: relative;
  }
  .card {
    position: absolute;
    left: 250px;
    width: 700px;
    height: 400px;
    background: var(--card);
    box-shadow: 0 6px 18px var(--shade);
  }
  .card--back { top: 35px; }
  .card--front { top: 465px; }

  /* Company name block, shared */
  .company {
    display: flex;
    flex-direction: column;
    align-items: center;
    font-weight: 800;
    text-transform: uppercase;
    color: var(--ink);
    line-height: 1;
  }
  .company__main { font-size: 36px; letter-spacing: 0.5px; }
  .company__sub { font-size: 21px; letter-spacing: 0.6px; margin-top: 4px; }
  .company__legal {
    display: flex;
    align-items: center;
    gap: 10px;
    width: 100%;
    margin-top: 5px;
    font-size: 12px;
    letter-spacing: 1px;
  }
  .company__legal::before,
  .company__legal::after {
    content: "";
    flex: 1;
    height: 2px;
    background: var(--ink-soft);
  }

  /* Back */
  .brand {
    position: absolute;
    top: 62px;
    left: 0; right: 0;
    display: flex;
    justify-content: center;
    align-items: center;
    gap: 24px;
  }
  .brand__dot {
    width: 104px; height: 104px;
    border-radius: 50%;
    background: var(--ink);
    flex: none;
  }
  .brand__text { display: flex; flex-direction: column; align-items: center; }
  .brand__tag {
    margin-top: 12px;
    font-size: 15px;
    color: var(--ink-soft);
  }
  .write-line {
    position: absolute;
    left: 150px; right: 110px;
    height: 1px;
    background: var(--rule);
  }
  .write-line--one { top: 242px; }
  .write-line--two { top: 292px; }
  .back-note {
    position: absolute;
    left: 0; right: 0;
    bottom: 42px;
    text-align: center;
    font-size: 17px;
    letter-spacing: 0.4px;
    color: var(--ink-soft);
  }

  /* Front */
  .front-info {
    position: absolute;
    top: 92px; left: 50px;
    width: 340px;
    display: flex;
    flex-direction: column;
    align-items: flex-start;
  }
  .front-info .company { width: 300px; }
  .company__underline {
    width: 300px;
    height: 2px;
    margin-top: 10px;
    background: var(--ink-soft);
  }
  .person {
    margin-top: 26px;
    margin-left: 10px;
    font-weight: 800;
    font-size: 21px;
    text-transform: uppercase;
    letter-spacing: 0.3px;
  }
  .contacts {
    margin-top: 12px;
    margin-left: 10px;
    list-style: none;
    font-size: 15px;
    color: var(--ink-soft);
  }
  .contacts li { display: flex; align-items: center; gap: 10px; margin-bottom: 8px; }
  .contacts svg { width: 18px; height: 18px; flex: none; }
  .address {
    margin-top: 14px;
    margin-left: 10px;
    font-size: 16px;
    color: var(--ink-soft);
  }
  .sheep-art {
    position: absolute;
    top: 20px; right: 20px;
    width: 280px; height: 360px;
    background: radial-gradient(ellipse at 55% 45%, var(--art-light) 0%, var(--art-dark) 100%);
    border-radius: 4px;
  }
</style>
</head>
<body>

  <section class="card card--back" aria-label="Business card back">
    <div class="brand">
      <div class="brand__dot"></div>
      <div class="brand__text">
        <div class="company">
          <span class="company__main">Ram and Co</span>
          <span class="company__sub">Fleecing Works</span>
          <span class="company__legal">Pty Ltd</span>
        </div>
        <p class="brand__tag">Gippsland shearing contractor</p>
      </div>
    </div>
    <div class="write-line write-line--one"></div>
    <div class="write-line write-line--two"></div>
    <p class="back-note">Professional shearing contract offering full contract team.</p>
  </section>

  <section class="card card--front" aria-label="Business card front">
    <div class="front-info">
      <div class="company">
        <span class="company__main">Ram and Co</span>
        <span class="company__sub">Fleecing Works</span>
        <span class="company__legal">Pty Ltd</span>
      </div>
      <div class="company__underline"></div>
      <p class="person">Marcus Haldenby</p>
      <ul class="contacts">
        <li>
          <svg viewBox="0 0 24 24" aria-hidden="true"><path fill="#1e1e1e" d="M6.6 10.8a15 15 0 0 0 6.6 6.6l2.2-2.2a1 1 0 0 1 1-.25 11.4 11.4 0 0 0 3.6.57 1 1 0 0 1 1 1V20a1 1 0 0 1-1 1A17 17 0 0 1 3 4a1 1 0 0 1 1-1h3.5a1 1 0 0 1 1 1c0 1.250.2 2.45.57 3.57a1 1 0 0 1-.25 1z"/></svg>
          0471305846
        </li>
        <li>
          <svg viewBox="0 0 24 24" aria-hidden="true"><rect x="2" y="5" width="20" height="14" fill="#1e1e1e"/><path d="M2 5l10 8 10-8" fill="none" stroke="#fff" stroke-width="1.6"/></svg>
          ramandcofleecing@mailbarn.example
        </li>
      </ul>
      <p class="address">PO box 4072 sale vic 3853</p>
    </div>
    <div class="sheep-art" role="img" aria-label="Black line drawing of an Australian sheep standing in profile"></div>
  </section>

</body>
</html>
```